Stationery Set for Velmora Company

I need to create full stationery design for my company; Business Cards, Envelops, Letter Heads, Calendar.
In the letter head and Envelops... only contact information and website links.
Our company is a Service Management company with different domains of innovative services including Technology Service Management, Education Services, Outsourcing Management, Events Management.
I need a modern and innovative design specially for the business card. I some transparent designs and I like it, but don't limit your innovation to what I mentioned. Sky is limit for your innovation.

Target Market(s)

Middle East & Africa

Industry/Entity Type

Business Management

Colors
34a7d8
0355a3
85acd3
86cae7
cee9f5
cfdeed
e4daeb
f3f1f8
ecf7fb

Requirements
Must have
• Name, Title, Email, Mobile
Nice to have
• We have multiple locations in USA, KSA, EGY, so I need ideas about how to include all contact details maybe QR / Barcode or something else.
• Please see our locations and contact information: www.brightvelmora.example
Should not have
• Too much text

```html
<!DOCTYPE html>
<html lang="en">
<head>
<meta charset="utf-8">
<title>Velmora Company Stationery</title>
<link rel="stylesheet" href="https://fonts.googleapis.com/css2?family=Arimo:wght@400;700&family=Orbitron:wght@500&display=swap">
<style>
  :root {
    --bg: #eceef0;
    --paper: #ffffff;
    --ink: #3a3a3a;
    --ink-soft: #6b6b6b;
    --brand: #3b6fe0;
    --blue-deep: #2f3fa8;
    --blue-mid: #1f6fd0;
    --blue-sky: #19a8e6;
  }
  * { margin: 0; padding: 0; box-sizing: border-box; }
  html, body { width: 1200px; height: 937px; overflow: hidden; background: var(--bg); }
  body { font-family: "Arimo", Arial, sans-serif; color: var(--ink); }
  .canvas { position: relative; width: 1200px; height: 937px; }
  .sheet { position: absolute; background: var(--paper); overflow: hidden; }
  .band {
    position: absolute; left: 0; bottom: 0; width: 100%;
    background: linear-gradient(90deg, var(--blue-deep) 0%, var(--blue-mid) 35%, var(--blue-sky) 60%, var(--blue-mid) 85%, var(--blue-deep) 100%);
  }
  .brand-name { color: var(--brand); font-weight: 700; white-space: nowrap; display: flex; align-items: center; gap: 6px; }
  .brand-name .mark { display: inline-block; background: var(--brand); }

  /* Letterhead */
  .letterhead { left: 185px; top: 68px; width: 385px; height: 544px; }
  .letterhead .brand-name { position: absolute; left: 18px; top: 28px; font-size: 15px; }
  .letterhead .brand-name .mark { width: 9px; height: 9px; }
  .letterhead .band { height: 70px; }
  .contact { position: absolute; right: 18px; top: 22px; text-align: right; font-size: 5.5px; line-height: 8px; color: var(--ink); }
  .contact .phone { font-size: 7px; }
  .letter { position: absolute; left: 36px; top: 137px; width: 300px; font-size: 5.2px; line-height: 7.3px; color: var(--ink-soft); }
  .letter p { margin-bottom: 10px; }
  .letter .date, .letter .greeting, .letter .sign-name { color: var(--ink); }
  .letter .greeting, .letter .sign-name { font-weight: 700; }
  .letter .closing { margin-bottom: 6px; }
  .signature-line { width: 30px; height: 12px; margin-bottom: 4px; }

  /* Folder */
  .folder { left: 636px; top: 40px; width: 458px; height: 576px; }
  .folder .brand-name { position: absolute; left: 0; right: 0; top: 290px; justify-content: center; font-size: 28px; }
  .folder .brand-name .mark { width: 16px; height: 16px; }
  .folder .band { height: 72px; }

  /* Business cards */
  .card-front { left: 45px; top: 658px; width: 177px; height: 101px; }
  .card-front .brand-name { position: absolute; left: 10px; top: 22px; font-size: 8.5px; gap: 4px; }
  .card-front .brand-name .mark { width: 5px; height: 5px; }
  .card-front .band { height: 20px; }
  .card-details { position: absolute; left: 99px; top: 15px; font-size: 4.4px; line-height: 5.8px; }
  .card-details .person { font-weight: 700; font-size: 5px; }
  .card-details .role { margin-bottom: 4px; color: var(--ink-soft); }
  .card-front .web { position: absolute; right: 6px; bottom: 5px; font-size: 3.8px; color: #ffffff; }
  .card-back { left: 45px; top: 785px; width: 177px; height: 100px; }
  .card-back .brand-name { position: absolute; left: 0; right: 0; top: 43px; justify-content: center; font-size: 9.5px; gap: 4px; }
  .card-back .brand-name .mark { width: 5px; height: 5px; }

  /* Envelopes */
  .envelope-front { left: 265px; top: 672px; width: 430px; height: 207px; }
  .envelope-front .brand-name { position: absolute; left: 16px; top: 28px; font-size: 14px; }
  .envelope-front .brand-name .mark { width: 8px; height: 8px; }
  .envelope-front .band { height: 78px; }
  .envelope-back { left: 737px; top: 672px; width: 431px; height: 207px; }
  .envelope-back .band { top: 0; bottom: auto; height: 66px; }
  .envelope-back .web { position: absolute; left: 0; right: 0; top: 26px; text-align: center; font-family: "Orbitron", "Arimo", sans-serif; font-size: 12px; letter-spacing: 1.6px; color: #ffffff; }
</style>
</head>
<body>
<div class="canvas">

  <!-- Letterhead -->
  <section class="sheet letterhead">
    <div class="brand-name"><span class="mark"></span>Velmora Company</div>
    <div class="contact">
      <div>14 Cedar Tower,</div>
      <div>Harbor Road</div>
      <div class="phone">012 555 0148 &#9742;</div>
      <div>hello@velmora.example &#9993;</div>
    </div>
    <div class="letter">
      <div class="date">July 2, 2012</div>
      <div class="greeting">Dear Client,</div>
      <p>Lotus Building, Palm St., Riverton</p>
      <p>We are pleased to confirm the details of our recent discussion regarding the service review for your team. Our consultants will prepare a short summary of the findings and share the proposed schedule for the next phase. Please review the attached notes and let us know if any changes are needed before the planning meeting later this month.</p>
      <p>We appreciate your continued trust and look forward to working together on the next steps of this project.</p>
      <p>Our team will remain available to answer any questions during the transition period. We will also arrange a brief session to walk your staff through the updated process and the new reporting tools. A follow-up report will be delivered within two weeks, and we welcome any feedback that helps us improve our services.</p>
      <p class="closing">Best Regards,</p>
      <svg class="signature-line" viewBox="0 0 30 12" aria-hidden="true"><line x1="1" y1="10" x2="29" y2="10" stroke="#222" stroke-width="0.6"/></svg>
      <div class="sign-name">Daniel Reyes</div>
      <div>Director</div>
      <div>Lotus Building, Palm St., Riverton</div>
    </div>
    <div class="band" role="img" aria-label="Decorative blue and grey band artwork"></div>
  </section>

  <!-- Presentation folder -->
  <section class="sheet folder">
    <div class="brand-name"><span class="mark"></span>Velmora Company</div>
    <div class="band" role="img" aria-label="Decorative blue and grey band artwork"></div>
  </section>

  <!-- Business card front -->
  <section class="sheet card-front">
    <div class="brand-name"><span class="mark"></span>Velmora Company</div>
    <div class="card-details">
      <div class="person">SAMIR HADDAD</div>
      <div class="role">Managing Director</div>
      <div>14 Cedar Tower,</div>
      <div>Harbor Road</div>
      <div style="margin-top:3px">&#9742; 012 555 0148</div>
      <div>&#9993; hello@velmora.example</div>
    </div>
    <div class="band" role="img" aria-label="Decorative blue and grey band artwork"></div>
    <div class="web">www.brightvelmora.example</div>
  </section>

  <!-- Business card back -->
  <section class="sheet card-back">
    <div class="brand-name"><span class="mark"></span>Velmora Company</div>
  </section>

  <!-- Envelope front -->
  <section class="sheet envelope-front">
    <div class="brand-name"><span class="mark"></span>Velmora Company</div>
    <div class="band" role="img" aria-label="Decorative blue and grey band artwork"></div>
  </section>

  <!-- Envelope back -->
  <section class="sheet envelope-back">
    <div class="band" role="img" aria-label="Decorative blue flap artwork"></div>
    <div class="web">www.brightvelmora.example</div>
  </section>

</div>
</body>
</html>
```